Business Card Design for Flood Rescue 360 - Property Restoration Professionals

I need a business card designed for Flood Rescue 360. We are a full-service property restoration solution. Providing water, fire, smoke & storm restoration as well as mold remediation and full remodel or reconstruction to homes and businesses across Dallas-Fort Worth, TX.
Target Market(s)
home and business owners with insurance covered property damage from water, fire or storm related damage
Industry/Entity Type
property restoration
Contact Information for Business Card
Marcus Pelley General Manager Cell: 214-555-0193 Office: 469-555-0148 email: Marcus@FloodRescue360.example services: Water, Fire, Mold, Reconstruction Tagline: Fast Response When Water Strikes!
Look and feel
Each slider illustrates characteristics of the customer's brand and the style your logo design should communicate.

```html
<!DOCTYPE html>
<html lang="en">
<head>
<meta charset="utf-8">
<title>Flood Rescue 360 – Business Card</title>
<link href="https://fonts.googleapis.com/css2?family=Montserrat:wght@400;600;800&family=Oswald:wght@500;600&family=Ubuntu:wght@700&display=swap" rel="stylesheet">
<style>
  :root {
    --brand-blue: #00b2e6;
    --ink: #1c1c1c;
    --card-white: #ffffff;
    --card-black: #1e1e1e;
    --backdrop: #3a3a3c;
  }
  * { box-sizing: border-box; margin: 0; padding: 0; }
  html, body { width: 1200px; height: 1200px; overflow: hidden; }
  body {
    background: var(--backdrop);
    font-family: "Montserrat", sans-serif;
    position: relative;
  }
  .card {
    position: absolute;
    left: 150px;
    width: 900px;
    height: 515px;
    border-radius: 40px;
    overflow: hidden;
    box-shadow: 0 14px 30px rgba(0,0,0,0.45);
  }
  .card--front { top: 50px; background: var(--card-white); }
  .card--back { top: 630px; background: var(--card-black); border-bottom: 4px solid var(--brand-blue); }

  .identity { position: absolute; left: 80px; top: 130px; }
  .identity__name {
    color: var(--brand-blue);
    font-weight: 600;
    font-size: 46px;
    letter-spacing: 1px;
    line-height: 1;
    text-transform: uppercase;
  }
  .identity__title {
    color: var(--ink);
    font-size: 25px;
    letter-spacing: 1px;
    text-transform: uppercase;
    margin-top: 2px;
  }
  .contacts { position: absolute; left: 80px; top: 232px; list-style: none; }
  .contacts li {
    display: flex; align-items: center; gap: 18px;
    font-size: 26px; color: var(--ink); height: 46px;
  }
  .contacts svg { width: 30px; height: 30px; flex: none; }

  .services { position: absolute; left: 560px; top: 70px; font-family: "Oswald", sans-serif; }
  .services__heading { color: var(--brand-blue); font-size: 30px; font-weight: 500; letter-spacing: 0.5px; }
  .services__list { list-style: none; }
  .services__list li {
    color: var(--ink); font-size: 30px; font-weight: 600; line-height: 1.15;
    text-transform: uppercase; display: flex; align-items: center; gap: 12px;
  }
  .services__list li::before {
    content: ""; width: 10px; height: 10px; border-radius: 50%; background: var(--brand-blue);
  }

  .tagline-band {
    position: absolute; left: 0; right: 0; top: 385px; height: 72px;
    background: var(--brand-blue);
    display: flex; align-items: center; justify-content: center;
  }
  .tagline-band p {
    font-family: "Ubuntu", sans-serif; font-weight: 700; font-size: 32px;
    color: var(--card-white); letter-spacing: 1px;
  }
  .base-stripe {
    position: absolute; left: 0; right: 0; top: 470px; bottom: 0;
    background: var(--brand-blue);
  }

  .brand {
    position: absolute; inset: 0;
    display: flex; align-items: center; justify-content: center; gap: 26px;
  }
  .brand__dot { width: 70px; height: 70px; border-radius: 50%; background: var(--brand-blue); }
  .brand__name {
    font-family: "Montserrat", sans-serif; font-weight: 800; font-size: 66px;
    color: var(--brand-blue); text-transform: uppercase; letter-spacing: 1px;
  }
</style>
</head>
<body>

<section class="card card--front">
  <div class="identity">
    <h1 class="identity__name">Marcus Pelley</h1>
    <p class="identity__title">General Manager</p>
  </div>

  <ul class="contacts">
    <li>
      <svg viewBox="0 0 30 30" aria-hidden="true"><rect x="8" y="2" width="14" height="26" rx="3" fill="none" stroke="#00b2e6" stroke-width="2.5"/><line x1="13" y1="24" x2="17" y2="24" stroke="#00b2e6" stroke-width="2.5"/></svg>
      214-555-0193
    </li>
    <li>
      <svg viewBox="0 0 30 30" aria-hidden="true"><path d="M7 3 L12 3 L14 10 L10.5 12.5 Q13 18 17.5 19.5 L20 16 L27 18 L27 23 Q26 27 21 27 Q5 24 3 8 Q3 3 7 3 Z" fill="#00b2e6"/></svg>
      469-555-0148
    </li>
    <li>
      <svg viewBox="0 0 30 30" aria-hidden="true"><rect x="2" y="7" width="26" height="17" fill="#00b2e6"/><path d="M2 7 L15 17 L28 7" fill="none" stroke="#fff" stroke-width="2"/></svg>
      Marcus@FloodRescue360.example
    </li>
  </ul>

  <div class="services">
    <h2 class="services__heading">SERVICES:</h2>
    <ul class="services__list">
      <li>Water</li>
      <li>Fire</li>
      <li>Mold</li>
      <li>Reconstruction</li>
    </ul>
  </div>

  <div class="tagline-band"><p>Fast Response When Water Strikes!</p></div>
  <div class="base-stripe"></div>
</section>

<section class="card card--back">
  <div class="brand">
    <span class="brand__name">Flood Rescue 360</span>
    <span class="brand__dot"></span>
  </div>
</section>

</body>
</html>
```